Book Cover with this title and sub title
Where Auntie Found Her Quiet Orchard
A small guide to spend wisely with your savings and care for the planet.
Walter P. Brunk Ph. D.
Ellen R. Brunk
Picture below would be on the entire front cover. Words somehow incorporated for easy reading.

```html
<!DOCTYPE html>
<html lang="en">
<head>
<meta charset="utf-8">
<title>Where Auntie Found Her Quiet Orchard — Book Cover</title>
<link rel="stylesheet" href="https://fonts.googleapis.com/css2?family=Bebas+Neue&family=Cinzel:wght@400&family=Roboto+Condensed:wght@700&display=swap">
<style>
  :root {
    --backdrop: #c3d4de;
    --cover-olive-light: #807c61;
    --cover-olive: #6e6a52;
    --cover-olive-dark: #4f4c3c;
    --bloom-yellow: #e8d230;
    --bloom-gold: #d9b21a;
    --stem-green: #5f6e3c;
    --type-white: #f1f1ee;
  }
  * { margin: 0; padding: 0; box-sizing: border-box; }
  html, body {
    width: 1200px;
    height: 1151px;
    overflow: hidden;
    background: var(--backdrop);
  }
  .canvas {
    position: relative;
    width: 1200px;
    height: 1151px;
  }
  .book-cover {
    position: absolute;
    left: 230px;
    top: 25px;
    width: 740px;
    height: 1100px;
    overflow: hidden;
    box-shadow: 0 10px 30px rgba(40, 55, 65, 0.25);
  }
  .cover-photo {
    position: absolute;
    inset: 0;
    width: 100%;
    height: 100%;
  }
  .title-block {
    position: absolute;
    top: 270px;
    left: 0;
    width: 100%;
    text-align: center;
    color: var(--type-white);
    text-shadow: 0 3px 8px rgba(0, 0, 0, 0.35);
  }
  .title-lead,
  .title-link,
  .title-main {
    display: block;
  }
  .title-lead {
    font-family: "Bebas Neue", sans-serif;
    font-size: 64px;
    font-weight: 400;
    letter-spacing: 1px;
    line-height: 1;
  }
  .title-link {
    font-family: "Cinzel", serif;
    font-size: 30px;
    font-weight: 400;
    letter-spacing: 8px;
    line-height: 1;
    margin-top: 14px;
  }
  .title-main {
    font-family: "Bebas Neue", sans-serif;
    font-size: 170px;
    font-weight: 400;
    line-height: 0.9;
    letter-spacing: 2px;
    margin-top: 8px;
  }
  .subtitle {
    font-family: "Bebas Neue", sans-serif;
    font-size: 36px;
    line-height: 1.1;
    letter-spacing: 0.5px;
    margin: 22px auto 0;
    width: 560px;
  }
  .authors {
    position: absolute;
    bottom: 70px;
    left: 0;
    width: 100%;
    text-align: center;
    font-family: "Roboto Condensed", sans-serif;
    font-weight: 700;
    font-size: 40px;
    letter-spacing: 8px;
    line-height: 1.35;
    color: var(--type-white);
    text-transform: uppercase;
    text-shadow: 0 2px 6px rgba(0, 0, 0, 0.35);
  }
</style>
</head>
<body>
<main class="canvas">
  <section class="book-cover">
    <svg class="cover-photo" viewBox="0 0 740 1100" preserveAspectRatio="none" role="img" aria-label="Full-cover photograph of a honeybee gathering pollen on small yellow flowers against a soft blurred olive background">
      <defs>
        <linearGradient id="coverBase" x1="0" y1="0" x2="0.4" y2="1">
          <stop offset="0" stop-color="var(--cover-olive-light)"/>
          <stop offset="0.55" stop-color="var(--cover-olive)"/>
          <stop offset="1" stop-color="var(--cover-olive-dark)"/>
        </linearGradient>
        <radialGradient id="bloomGlow" cx="0.5" cy="0.5" r="0.5">
          <stop offset="0" stop-color="var(--bloom-yellow)" stop-opacity="0.95"/>
          <stop offset="0.55" stop-color="var(--bloom-gold)" stop-opacity="0.55"/>
          <stop offset="1" stop-color="var(--bloom-gold)" stop-opacity="0"/>
        </radialGradient>
        <radialGradient id="stemGlow" cx="0.5" cy="0.5" r="0.5">
          <stop offset="0" stop-color="var(--stem-green)" stop-opacity="0.6"/>
          <stop offset="1" stop-color="var(--stem-green)" stop-opacity="0"/>
        </radialGradient>
      </defs>
      <rect width="740" height="1100" fill="url(#coverBase)"/>
      <ellipse cx="470" cy="960" rx="180" ry="160" fill="url(#stemGlow)"/>
      <ellipse cx="400" cy="720" rx="300" ry="260" fill="url(#bloomGlow)"/>
    </svg>

    <header class="title-block">
      <h1>
        <span class="title-lead">Where Auntie Found</span>
        <span class="title-link">HER QUIET</span>
        <span class="title-main">ORCHARD</span>
      </h1>
      <p class="subtitle">A small guide to spend wisely with your savings and care for the planet.</p>
    </header>

    <p class="authors">Walter P. Brunk Ph. D.<br>Ellen R. Brunk</p>
  </section>
</main>
</body>
</html>
```